Business Card Design

I am a realtor and i also flip houses. I am CEO and Founder of my business which is Voskell Group LLC which is named after my great uncle who died and i was really close to. He was a wonderful friendly man so i want my business to represent him too. My business works with a lot of different people but i want mainly something to show i am a strong confidant woman who owns there own business. I have a really fun personality so i don't want anything TOO serious or manly. I want the perfect mix. My last two business cards i created are too embarrassing to hand out because they are far too girly and i deal with a lot of millionaire clients. I live out in the Palm Springs California area. I think its very important to show i am a single mom, female with her own business at only 24. I don't want to just be a female that blends in with all of the other serious people but yet i don't want to seem immature. People are telling me to stay away from pinks and purples but i don't want blues and greens because they represent men more. But i won't say no to them if there is a happy medium.

Industry/Entity Type

Realtor

Contact Information for Business Card

Voskell Group, LLC
Corinne Tabb
27358 Halvern Ave, C2 517
Rancho Mirage, CA 92270
760-419-6735
Corinnedtabb@mailvane.com

```html
<!DOCTYPE html>
<html lang="en">
<head>
<meta charset="utf-8">
<title>Voskell Group LLC – Corinne Tabb</title>
<link rel="stylesheet" href="https://fonts.googleapis.com/css2?family=Aldrich&display=swap">
<style>
  :root {
    --teal: #00959e;
    --teal-dark: #00727a;
    --pink: #f99ccb;
    --mint: #a9e2b6;
    --sky: #a3dbe8;
    --ice: #bdebf0;
  }
  html, body {
    margin: 0;
    padding: 0;
    width: 1200px;
    height: 702px;
    overflow: hidden;
    background: var(--teal);
  }
  .business-card {
    display: block;
    width: 1200px;
    height: 702px;
  }
  .card-text {
    font-family: "Aldrich", "Share Tech", sans-serif;
  }
  .company-name { fill: var(--mint); font-size: 44px; }
  .person-name { fill: var(--mint); font-size: 40px; }
  .address-line { fill: var(--sky); font-size: 30px; }
  .phone-number { fill: var(--sky); font-size: 30px; }
  .email-address { fill: var(--ice); font-size: 29px; }
  .frame-band { fill: var(--pink); }
  .card-field { fill: var(--teal); }
  .contact-icon { fill: var(--teal-dark); }
</style>
</head>
<body>
<svg class="business-card" viewBox="0 0 1085 634" preserveAspectRatio="none" xmlns="http://www.w3.org/2000/svg" aria-label="Business card for Corinne Tabb, Voskell Group LLC">
  <rect class="card-field" x="0" y="0" width="1085" height="634"/>

  <!-- pink frame -->
  <path class="frame-band" fill-rule="evenodd"
        d="M14 14 H1073 V622 H14 Z M30 42 V592 H1045 V42 Z"/>
  <!-- diagonal band -->
  <polygon class="frame-band" points="1000,42 1045,42 440,600 395,600"/>

  <!-- header -->
  <text class="card-text company-name" x="470" y="130">Voskell Group LLC</text>
  <text class="card-text person-name" x="390" y="205">Corinne Tabb</text>

  <!-- address -->
  <text class="card-text address-line" x="303" y="288">27358 Halvern Ave</text>
  <text class="card-text address-line" x="224" y="368">C2 517 Rancho Mirage</text>
  <text class="card-text address-line" x="165" y="443">CA 92270</text>

  <!-- phone -->
  <g class="contact-icon" transform="translate(70 554)">
    <path d="M6 2 L13 0 L18 11 L13 15 C15 21 19 25 25 27 L29 22 L40 27 L38 34 C37 36 35 37 32 36 C17 33 5 21 2 7 C1 5 3 3 6 2 Z"/>
  </g>
  <text class="card-text phone-number" x="130" y="582">760-419-6735</text>

  <!-- email -->
  <g class="contact-icon" transform="translate(562 526) rotate(-43.6)">
    <rect x="-22" y="-15" width="44" height="30" rx="2"/>
    <polyline points="-20,-13 0,3 20,-13" fill="none" stroke="var(--teal)" stroke-width="2.5"/>
  </g>
  <text class="card-text email-address" x="612" y="500" textLength="440" lengthAdjust="spacingAndGlyphs"
        transform="rotate(-43.6 612 500)">corinnedtabb@mailvane.com</text>
</svg>
</body>
</html>
```